Unique Business Card Design

Unique Business Card design for our orthotic and prosthetic company. Our logo is on our website, color is light blue. Unique shape (artificial leg shaped, vertical, etc..) preferred. Logo, business name, individual name and basic demographics needed.

Industry/Entity Type

Business

Contact Information for Business Card

Logo, Industry, Phone # Logo, "Prosthetic & Orthotic Services" Place to add individual name and contact info

Colors
cee9f5

Requirements
Must have
• The icon must be there, placement of "Prosthetic & Orthotic Services" can be moved
Nice to have
• Like the mix of light blue, and a little darker blue. One design included the icons from my website which was a nice touch

```html
<!DOCTYPE html>
<html lang="en">
<head>
<meta charset="utf-8">
<title>Limbwell Inc – Business Card</title>
<link href="https://fonts.googleapis.com/css2?family=Open+Sans:wght@400;600;700&display=swap" rel="stylesheet">
<style>
  :root {
    --page-bg: #e8ecef;
    --card-light: #d2e9f6;
    --brand-blue: #0f72cf;
    --brand-text: #1b6fc3;
    --stripe-dark: #0a0a0a;
    --on-blue: #ffffff;
  }
  html, body {
    margin: 0;
    width: 1200px;
    height: 900px;
    overflow: hidden;
    background: var(--page-bg);
    font-family: "Open Sans", sans-serif;
  }
  .business-card {
    position: absolute;
    left: 100px;
    top: 141px;
    width: 1000px;
    height: 618px;
    background: var(--card-light);
    overflow: hidden;
    box-shadow: 0 10px 30px rgba(0,0,0,0.15);
  }
  .wave-band {
    position: absolute;
    inset: 0;
    width: 1000px;
    height: 618px;
  }
  .brand-mark {
    position: absolute;
    left: 63px;
    top: 89px;
    width: 144px;
    height: 144px;
    border-radius: 50%;
    background: var(--brand-blue);
  }
  .brand-name {
    position: absolute;
    left: 245px;
    top: 118px;
    margin: 0;
    font-size: 42px;
    font-weight: 600;
    line-height: 1;
    letter-spacing: 0.5px;
    color: var(--brand-text);
  }
  .brand-rule {
    position: absolute;
    left: 248px;
    top: 167px;
    width: 368px;
    height: 3px;
    background: var(--brand-text);
  }
  .brand-tagline {
    position: absolute;
    left: 248px;
    top: 176px;
    width: 368px;
    margin: 0;
    text-align: center;
    font-size: 21px;
    color: var(--brand-text);
  }
  .contact-block {
    position: absolute;
    right: 50px;
    top: 282px;
    text-align: right;
    color: var(--on-blue);
  }
  .person-name {
    margin: 0;
    font-size: 32px;
    font-weight: 600;
    line-height: 1.2;
  }
  .person-title {
    margin: 0 0 20px;
    font-size: 25px;
    line-height: 1.3;
  }
  .contact-line {
    display: flex;
    justify-content: flex-end;
    align-items: center;
    gap: 8px;
    margin: 0;
    font-size: 26px;
    line-height: 1.42;
  }
  .contact-line.phone {
    font-size: 30px;
    font-weight: 600;
  }
  .contact-line svg {
    width: 20px;
    height: 20px;
    fill: var(--on-blue);
  }
  .address {
    position: absolute;
    right: 50px;
    top: 520px;
    margin: 0;
    font-size: 26px;
    color: var(--on-blue);
  }
</style>
</head>
<body>
  <div class="business-card">
    <svg class="wave-band" viewBox="0 0 652 403" preserveAspectRatio="none" aria-hidden="true">
      <path fill="var(--stripe-dark)" d="M0,209 C120,284 200,314 300,274 C400,234 470,112 560,108 C610,106 640,134 652,160 L652,403 L0,403 Z"/>
      <path fill="var(--card-light)" d="M0,219 C120,294 200,324 300,284 C400,244 470,124 560,120 C610,118 640,146 652,168 L652,403 L0,403 Z"/>
      <path fill="var(--brand-blue)" d="M0,226 C120,301 200,331 300,291 C400,251 470,132 560,128 C610,126 640,152 652,174 L652,403 L0,403 Z"/>
    </svg>

    <div class="brand-mark" aria-hidden="true"></div>
    <h1 class="brand-name">LIMBWELL INC</h1>
    <div class="brand-rule"></div>
    <p class="brand-tagline">Prosthetic &amp; Orthotic Services</p>

    <div class="contact-block">
      <p class="person-name">Daniel Hart</p>
      <p class="person-title">Managing Director</p>
      <p class="contact-line phone">(555) 014-2290
        <svg viewBox="0 0 24 24" aria-hidden="true"><path d="M6.6 10.8a15.1 15.1 0 0 0 6.6 6.6l2.2-2.2a1 1 0 0 1 1-.25 11.4 11.4 0 0 0 3.6.57 1 1 0 0 1 1 1V20a1 1 0 0 1-1 1A17 17 0 0 1 3 4a1 1 0 0 1 1-1h3.5a1 1 0 0 1 1 1c0 1.25.2 2.45.57 3.57a1 1 0 0 1-.25 1z"/></svg>
      </p>
      <p class="contact-line">info@limbwellinc.com
        <svg viewBox="0 0 24 24" aria-hidden="true"><path d="M2 5h20v14H2z M3.5 6.5 12 13l8.5-6.5" stroke="var(--brand-blue)" stroke-width="1.5"/></svg>
      </p>
      <p class="contact-line">www.limbwellinc.com
        <svg viewBox="0 0 24 24" aria-hidden="true"><circle cx="12" cy="12" r="10"/><path d="M2 12h20M12 2c3 3 3 17 0 20M12 2c-3 3-3 17 0 20" stroke="var(--brand-blue)" stroke-width="1.5" fill="none"/></svg>
      </p>
    </div>

    <p class="address">12345, Address Goes Here Country Name, 123456.</p>
  </div>
</body>
</html>
```